Management Consultancy needs sharp professional services showcased in a brochure

We are a management consultancy specializing on contract management and conflict avoidance services requiring a professional brochure showcasing our services to prospective clients.

Attached are a selection of existing stationary and the colour scheme.

Further details on our company can be found at www.velt-advisory-partners.com
Updates

Preference is for bi-fold, however, innovative tri-fold will be considered. Added Monday, August 7, 2017

Target Market(s)

Construction companies, consultants, developers, oil and gas service providers, NGO's, SME's.

Industry/Entity Type

Management

Requirements
Must have
• High degree of professionalism with eye catching, sharp detail. No frils.
• Colour scheme as per the attachments
• Font as per attachments - Century Gothic
• Details of our company and services
Nice to have
• Open to ideas, thinking along the lines of a car brochure type design.
• Bi-fold preferred, by trifold accepted if innovative.
Should not have
• Remove reference to the United Arab Emirates.
• No cartoon/clipart photos.

```html
<!DOCTYPE html>
<html lang="en">
<head>
<meta charset="utf-8">
<title>Velt Advisory – Founder &amp; Services</title>
<link rel="stylesheet" href="https://fonts.googleapis.com/css2?family=Didact+Gothic&family=Tinos:wght@400;700&display=swap">
<style>
  :root {
    --bg: #d9dadd;
    --paper: #f4f4f6;
    --paper-shade: #e6e7eb;
    --red: #9b1b24;
    --red-dark: #5e0f15;
    --navy: #1f2f57;
    --navy-dark: #111a33;
    --ink: #2a2a2e;
    --ink-soft: #4a4b52;
    --rule: #b23a42;
  }
  * { box-sizing: border-box; margin: 0; padding: 0; }
  html, body { width: 1200px; height: 789px; overflow: hidden; }
  body { background: var(--bg); font-family: "Tinos", serif; color: var(--ink); }

  .spread { position: absolute; left: 30px; top: 14px; width: 1140px; height: 761px; display: flex; box-shadow: 0 6px 24px rgba(0,0,0,.25); }
  .page { position: relative; width: 570px; height: 761px; background: var(--paper); overflow: hidden; }
  .page--left { background: linear-gradient(90deg, var(--paper) 88%, var(--paper-shade)); }
  .page--right { background: linear-gradient(90deg, var(--paper-shade), var(--paper) 12%); }

  .band { position: absolute; left: 0; top: 0; width: 570px; }

  /* Founder page */
  .founder-photo { position: absolute; left: 60px; top: 18px; width: 110px; height: 112px; background: linear-gradient(135deg, #dfe3ea, #a9b2c2); border: 3px solid #fff; }
  .page-title { position: absolute; font-family: "Didact Gothic", sans-serif; color: #fff; font-size: 22px; letter-spacing: 1px; text-transform: uppercase; }
  .page-title strong { font-weight: 700; }
  .founder-title { left: 240px; top: 40px; }
  .title-rule { position: absolute; height: 1px; background: rgba(255,255,255,.75); }
  .founder-name { position: absolute; left: 240px; top: 88px; font-family: "Didact Gothic", sans-serif; color: #fff; font-size: 14px; }

  .body-copy { position: absolute; font-size: 9.6px; line-height: 1.3; color: var(--ink-soft); text-align: justify; }
  .body-copy p { margin-bottom: 7px; }
  .founder-copy { left: 55px; top: 168px; width: 470px; }

  .section-head { font-family: "Didact Gothic", sans-serif; font-weight: 700; color: var(--red); font-size: 15px; text-transform: uppercase; letter-spacing: .5px; }
  .section-head span { color: var(--navy); }
  .bullets { list-style: none; font-size: 9.6px; line-height: 1.35; color: var(--ink-soft); }
  .bullets li { position: relative; padding-left: 12px; }
  .bullets li::before { content: ""; position: absolute; left: 0; top: 3px; border-left: 4px solid transparent; border-right: 4px solid transparent; border-bottom: 6px solid var(--red); }
  .memberships { position: absolute; left: 55px; top: 418px; width: 330px; }
  .memberships .section-head, .education .section-head { margin-bottom: 4px; }
  .education { position: absolute; left: 55px; top: 552px; width: 330px; }

  .chess-visual { position: absolute; left: 340px; top: 560px; width: 190px; height: 180px; background: radial-gradient(ellipse at 50% 60%, rgba(120,124,134,.45), rgba(244,244,246,0) 70%); }

  /* Services page */
  .services-title { left: 52px; top: 44px; }
  .services-panel { position: absolute; left: 40px; top: 100px; width: 490px; height: 640px; background: var(--paper); }
  .services-intro { left: 52px; top: 112px; width: 466px; }
  .advisory { position: absolute; left: 52px; width: 270px; }
  .advisory .section-head { font-size: 16px; margin-bottom: 6px; border-bottom: 1px solid var(--rule); padding-bottom: 2px; }
  .advisory .bullets { font-family: "Didact Gothic", sans-serif; font-size: 11.5px; color: var(--ink); line-height: 1.45; }
  .conflict { top: 228px; }
  .contract { top: 358px; }
  .puzzle-visual { position: absolute; left: 340px; top: 260px; width: 175px; height: 90px; background: linear-gradient(90deg, #fff 0%, #39407a 30%, #fff 50%, #39407a 75%, #fff 100%); opacity: .85; }
  .bulb-visual { position: absolute; left: 330px; top: 398px; width: 180px; height: 100px; background: radial-gradient(ellipse at 50% 45%, #e9e9ea, #6c6d72 55%, #1d1d20); }
  .commissions { position: absolute; left: 52px; top: 520px; width: 466px; }
  .commissions .section-head { font-size: 16px; border-bottom: 1px solid var(--rule); padding-bottom: 2px; width: 230px; margin-bottom: 6px; }
  .commissions .body-copy { position: static; margin-bottom: 8px; }
  .commission-list { list-style: none; font-family: "Didact Gothic", sans-serif; font-weight: 700; font-size: 11px; color: var(--navy); line-height: 1.5; }
  .commission-list li { position: relative; padding-left: 13px; }
  .commission-list li::before { content: ""; position: absolute; left: 0; top: 4px; border-left: 4px solid transparent; border-right: 4px solid transparent; border-bottom: 6px solid var(--red); }
</style>
</head>
<body>
<main class="spread">

  <section class="page page--left" aria-label="About our founder">
    <svg class="band" height="165" viewBox="0 0 570 165" aria-hidden="true">
      <defs>
        <linearGradient id="redBand" x1="0" x2="1">
          <stop offset="0" stop-color="#c22a33"/>
          <stop offset="1" stop-color="#5e0f15"/>
        </linearGradient>
      </defs>
      <path d="M0 0 H570 V140 Q300 110 0 155 Z" fill="url(#redBand)"/>
    </svg>
    <div class="founder-photo" role="img" aria-label="Portrait photograph of the founder in a business suit"></div>
    <h1 class="page-title founder-title">About <strong>Our Founder</strong></h1>
    <div class="title-rule" style="left:230px;top:74px;width:300px"></div>
    <p class="founder-name">Owen R. T. Hartley - Founder and Director</p>

    <div class="body-copy founder-copy">
      <p>Holding bases in Ireland and the United Kingdom, Owen brings a wealth of experience and knowledge to the business. Carrying over thirteen years' experience working for global consultants in construction, shipyards and service sectors, his portfolio spans complex offshore programmes, civil infrastructure and water projects across several regions, from large developments to smaller focused frameworks.</p>
      <p>He has fulfilled various senior roles in quantity surveying and commercial management, contract administration, claims preparation and dispute resolution, working directly with attorneys and engaging under multiple jurisdictions at local, national and international levels.</p>
      <p>Graduating part-time with honours in Quantity Surveying and Construction Economics, he later gained a diploma in Leadership and completed a master's in Construction Law and Arbitration, furthering his studies in commercial mediation and strategic negotiation with a focus on indemnity structures.</p>
      <p>He is currently studying for a diploma in Governance, Risk and Compliance and is undergoing a Masters in Law, Corporate Governance, Risk and Compliance.</p>
      <p>Owen is an accredited arbitrator and mediator and a certified dispute board member, and previously sat as a board member of a national building institute for a period of three years prior to stepping down.</p>
    </div>

    <div class="chess-visual" role="img" aria-label="Faded photograph of chess pieces"></div>

    <div class="memberships">
      <h2 class="section-head">Owen is a <span>member of:</span></h2>
      <ul class="bullets">
        <li>The Institute of Dispute Practitioners (Arbitration and Mediation);</li>
        <li>The Dispute Panel Alliance;</li>
        <li>The Northern Mediation Council;</li>
        <li>The Harbour Court of International Arbitration;</li>
        <li>The Society of Energy Engineers;</li>
        <li>The Global Association of Contract Management;</li>
        <li>The Compliance Standards Association; and</li>
        <li>The Open Mediation Network</li>
      </ul>
    </div>

    <div class="education">
      <h2 class="section-head">Graduating <span>establishments:</span></h2>
      <ul class="bullets">
        <li>Larkfield University - Northern Ireland, UK;</li>
        <li>Council of Service Education Boards, UK;</li>
        <li>Northgate University - Coastal Business School, Scotland, UK;</li>
        <li>Westmere University - Westmere Law School, UK;</li>
        <li>Lakeshore State University, USA;</li>
        <li>Redbridge University - Meridian Business School, UK;</li>
        <li>College of Law Studies - Ashcombe, UK (Ongoing).</li>
      </ul>
    </div>
  </section>

  <section class="page page--right" aria-label="Our services">
    <svg class="band" height="240" viewBox="0 0 570 240" aria-hidden="true">
      <defs>
        <linearGradient id="navyBand" x1="0" x2="1">
          <stop offset="0" stop-color="#111a33"/>
          <stop offset="1" stop-color="#3a4d7c"/>
        </linearGradient>
      </defs>
      <rect width="570" height="240" fill="url(#navyBand)"/>
    </svg>
    <h1 class="page-title services-title">Our <strong>Services</strong></h1>
    <div class="title-rule" style="left:52px;top:80px;width:230px"></div>
    <div class="services-panel"></div>

    <div class="body-copy services-intro">
      <p>Every contract has at least two parties; every party has a goal, and every goal matters. Each party must work in equilibrium as a contractual partnership or alliance, and where we are not party to the original agreement we provide effective objective insight to enhance all aspects of contract performance.</p>
      <p>We believe that a proactive approach to contract management creates transparency and trust, and maintains relationships and builds on them, addressing real and relevant issues early for timely resolution.</p>
    </div>

    <div class="advisory conflict">
      <h2 class="section-head">Conflict Advisory</h2>
      <ul class="bullets">
        <li>Restoration and Mediation Services.</li>
        <li>Shuttle Diplomacy Services and In Persona Intermediary Services.</li>
        <li>Negotiation Support Services.</li>
        <li>Workplace Mediation Services.</li>
      </ul>
    </div>
    <div class="puzzle-visual" role="img" aria-label="Photograph of two hands joining puzzle pieces"></div>

    <div class="advisory contract">
      <h2 class="section-head">Contract Advisory</h2>
      <ul class="bullets">
        <li>Contract Troubleshooting.</li>
        <li>Contracts Audit Services and Performance Management.</li>
        <li>Strategic Review &amp; Risk Assessment.</li>
        <li>Contract Fraud Investigation.</li>
      </ul>
    </div>
    <div class="bulb-visual" role="img" aria-label="Photograph of a row of light bulbs with one lit"></div>

    <div class="commissions">
      <h2 class="section-head">Commissions</h2>
      <p class="body-copy">At Velt Advisory, we pride ourselves on our versatility, providing a global reach with a local relationship; we ensure that our clients get the boutique service they deserve across a multitude of industries and locations, with our clients' interests always at the forefront of our minds.</p>
      <ul class="commission-list">
        <li>Construction - Marina District - Muscat, Oman</li>
        <li>Construction - Multi-Use Shipyard Facility, Duqm, Oman</li>
        <li>Shipyard - Offshore Drilling Unit, Dammam, Saudi Arabia</li>
        <li>Fabrication - Offshore Distribution Platform, Basra, Iraq</li>
        <li>Environmental Infrastructure - Waste Water Management, Belfast, N.Ireland</li>
        <li>Fabrication - Gas Compression Units, Atyrau, Kazakhstan</li>
        <li>Construction - Port Warehousing and Yard Facility, Luanda, Angola</li>
      </ul>
    </div>
  </section>

</main>
</body>
</html>
```